Book Cover Design RTM

Want a new book cover but want to use the same photo and change the sub name. This is for a brand called "Amber Meadow Living". The book is called "Quiet Steps, Bright Days"

This is for a 8.5 * 11 book size

We really want to brand the Amber Meadow Living

I've attached a sample of an old book cover, the photo I want used and the amber meadow living logo

Requirements
Must have
• Must have the logo,

must have the book title. "Quiet Steps, Bright Days"

Must have "Featuring" The Amber Meadow Living Tumble Card Game"

On the back put the logo and Amber Meadow Living Nutrition

must have the authors name "Norma Plaskett" on the page

"The Golden Stride Map"
Nice to have
• Amber Meadow Living Presents:

the book title

```html
<!DOCTYPE html>
<html lang="en">
<head>
<meta charset="utf-8">
<title>Quiet Steps, Bright Days — Cover</title>
<link rel="stylesheet" href="https://fonts.googleapis.com/css2?family=Heebo:wght@100;300&family=Source+Sans+3:wght@700&family=Poppins:wght@200;800&family=Barlow+Semi+Condensed:wght@400;600&display=swap">
<style>
  :root {
    --page-bg: #e8e8e8;
    --cover-black: #141414;
    --band-teal: #1fae8a;
    --band-teal-deep: #127a66;
    --band-grey: #4b4b4b;
    --band-grey-dark: #2e2e2e;
    --accent-yellow: #f1ea17;
    --text-white: #f4f4f4;
    --text-soft: #cfcfcf;
  }
  * { margin: 0; padding: 0; box-sizing: border-box; }
  html, body {
    width: 1200px; height: 862px; overflow: hidden;
    background: var(--page-bg);
  }
  .cover {
    position: absolute; left: 296px; top: 21px;
    width: 607px; height: 820px;
    background: var(--cover-black);
    overflow: hidden;
    font-family: "Barlow Semi Condensed", sans-serif;
    color: var(--text-white);
  }
  .band-teal {
    position: absolute; left: 0; top: 369px; width: 100%; height: 174px;
    background: linear-gradient(90deg, var(--band-teal) 0%, var(--band-teal-deep) 45%, var(--band-teal) 100%);
  }
  .band-grey {
    position: absolute; left: 0; top: 543px; width: 100%; height: 171px;
    background: linear-gradient(180deg, var(--band-grey-dark) 0%, var(--band-grey) 100%);
  }
  .cover-photo {
    position: absolute; left: 0; top: 290px; width: 395px; height: 424px;
    background: radial-gradient(ellipse at 30% 65%, #3fcfa4 0%, #1e8f74 35%, rgba(30,30,30,0.9) 75%);
    opacity: 0.85;
  }
  .brand-mark {
    position: absolute; right: 22px; top: 70px;
    font-family: "Heebo", sans-serif; font-weight: 300;
    font-size: 64px; letter-spacing: 6px; color: var(--text-soft);
  }
  .presents {
    position: absolute; right: 22px; top: 190px;
    font-family: "Heebo", sans-serif; font-weight: 300;
    font-size: 13.5px; color: var(--text-soft);
  }
  .title {
    position: absolute; right: 22px; top: 212px; text-align: right;
    text-transform: uppercase; line-height: 1;
  }
  .title-light {
    display: block;
    font-family: "Heebo", sans-serif; font-weight: 100;
    font-size: 68px; letter-spacing: -1px;
  }
  .title-bold {
    display: block; margin-top: 8px;
    font-family: "Source Sans 3", sans-serif; font-weight: 700;
    font-size: 58px; letter-spacing: 2px;
  }
  .subtitle {
    position: absolute; right: 22px; top: 400px; text-align: right;
    color: var(--accent-yellow); line-height: 1;
    font-family: "Poppins", sans-serif;
  }
  .subtitle-light { display: block; font-weight: 200; font-size: 40px; }
  .subtitle-bold { display: block; font-weight: 800; font-size: 36px; margin: 2px 0 0; }
  .feature {
    position: absolute; right: 22px; top: 570px; text-align: right; line-height: 1.05;
  }
  .feature-label { display: block; font-weight: 600; font-size: 25px; }
  .feature-line { display: block; font-weight: 400; font-size: 25px; }
  .feature-strong { display: block; font-weight: 600; font-size: 34px; }
  .author {
    position: absolute; right: 28px; top: 738px;
    font-size: 29px; font-weight: 400; color: var(--accent-yellow);
    text-transform: uppercase; letter-spacing: 0.5px;
  }
</style>
</head>
<body>
  <main class="cover">
    <div class="band-teal"></div>
    <div class="band-grey"></div>
    <div class="cover-photo" role="img" aria-label="Author photo: smiling woman in black sports bra and leggings leaning on a large teal exercise ball"></div>

    <div class="brand-mark">RTM</div>
    <p class="presents">Amber Meadow Living Presents</p>

    <h1 class="title">
      <span class="title-light">Quiet Steps,</span>
      <span class="title-bold">Bright Days</span>
    </h1>

    <h2 class="subtitle">
      <span class="subtitle-light">The</span>
      <span class="subtitle-bold">Golden Stride</span>
      <span class="subtitle-light">Map</span>
    </h2>

    <p class="feature">
      <span class="feature-label">"Featuring"</span>
      <span class="feature-line">The Amber Meadow Living</span>
      <span class="feature-strong">Tumble Card</span>
      <span class="feature-line">Game"</span>
    </p>

    <p class="author">Norma Plaskett</p>
  </main>
</body>
</html>
```